Business card design for my company.
I would like the card's background colour to be black. You can also see our web site to get an idea of our brand. https://www.tmwhomecrafting.com.au/
- Name
- Email

```html
<!DOCTYPE html>
<html lang="en">
<head>
<meta charset="utf-8">
<title>TMW Home Crafting – Business Card</title>
<link href="https://fonts.googleapis.com/css2?family=Poppins:wght@400;500;600;700&display=swap" rel="stylesheet">
<style>
  :root{
    --stage:#2b2c2d;
    --card-black:#050605;
    --green:#2f9a3e;
    --green-light:#4cb848;
    --green-dark:#1f7d33;
    --white:#f2f2f2;
    --faint:#1a1c1b;
    --divider:#5a5a5a;
  }
  *{margin:0;padding:0;box-sizing:border-box;}
  html,body{width:1200px;height:900px;overflow:hidden;}
  body{
    background:var(--stage);
    font-family:"Poppins",sans-serif;
    position:relative;
  }
  .card{
    position:absolute;
    left:260px;
    width:680px;
    height:390px;
    border-radius:34px;
    overflow:hidden;
  }
  .card--back{
    top:40px;
  }
  .back-pattern{
    position:absolute;inset:0;
    background:linear-gradient(120deg,var(--green-dark) 0%,var(--green-light) 50%,var(--green-dark) 100%);
  }
  .back-name{
    position:absolute;
    right:70px;top:180px;
    color:var(--white);
    font-weight:600;
    font-size:22px;
    letter-spacing:1px;
  }
  .card--front{
    top:470px;
    background:var(--card-black);
  }
  .front-watermark{
    position:absolute;
    right:40px;top:20px;
    color:var(--faint);
    font-weight:600;
    font-size:150px;
    line-height:1;
  }
  .person{
    position:absolute;
    left:42px;top:112px;
  }
  .person__name{
    color:var(--green);
    font-weight:700;
    font-size:22px;
    letter-spacing:.5px;
    text-transform:uppercase;
  }
  .person__title{
    color:var(--white);
    font-size:17px;
    margin-top:2px;
  }
  .brand{
    position:absolute;
    left:42px;top:250px;
    width:250px;
    color:var(--white);
    font-weight:600;
    font-size:30px;
    line-height:1.15;
    letter-spacing:1px;
    text-transform:uppercase;
  }
  .divider{
    position:absolute;
    left:318px;top:230px;
    width:1px;height:125px;
    background:var(--divider);
  }
  .contacts{
    position:absolute;
    left:342px;top:228px;
    list-style:none;
  }
  .contacts li{
    display:flex;align-items:center;
    gap:10px;
    color:var(--white);
    font-size:16px;
    height:31px;
  }
  .contacts svg{width:15px;height:15px;flex:none;}
  .hl{color:var(--green);}
</style>
</head>
<body>
  <section class="card card--back">
    <div class="back-pattern" role="img" aria-label="Repeating brand mark pattern on green"></div>
    <span class="back-name">TMW Home Crafting</span>
  </section>

  <section class="card card--front">
    <span class="front-watermark" aria-hidden="true">TMW</span>

    <div class="person">
      <p class="person__name">Liam Carver</p>
      <p class="person__title">General Manager</p>
    </div>

    <p class="brand">TMW Home Crafting</p>

    <div class="divider"></div>

    <ul class="contacts">
      <li>
        <svg viewBox="0 0 24 24" fill="var(--green)"><path d="M6.6 10.8a15 15 0 0 0 6.6 6.6l2.2-2.2a1 1 0 0 1 1-.25 11.4 11.4 0 0 0 3.6.57 1 1 0 0 1 1 1V20a1 1 0 0 1-1 1A17 17 0 0 1 3 4a1 1 0 0 1 1-1h3.5a1 1 0 0 1 1 1 11.4 11.4 0 0 0 .57 3.6 1 1 0 0 1-.25 1z"/></svg>
        0400 123 456
      </li>
      <li>
        <svg viewBox="0 0 24 24" fill="var(--green)"><path d="M2 5h20v14H2z M2 5l10 8 10-8" stroke="var(--card-black)" stroke-width="1.5"/></svg>
        <span>info@<span class="hl">tmwhomecrafting</span>.com.au</span>
      </li>
      <li>
        <svg viewBox="0 0 24 24" fill="none" stroke="var(--green)" stroke-width="2"><circle cx="12" cy="12" r="9"/><path d="M3 12h18M12 3c3 3 3 15 0 18M12 3c-3 3-3 15 0 18"/></svg>
        <span>www.<span class="hl">tmwhomecrafting</span>.com.au</span>
      </li>
      <li>
        <svg viewBox="0 0 24 24" fill="var(--green)"><path d="M12 2a7 7 0 0 0-7 7c0 5 7 13 7 13s7-8 7-13a7 7 0 0 0-7-7zm0 9.5A2.5 2.5 0 1 1 12 6.5a2.5 2.5 0 0 1 0 5z"/></svg>
        Kingsbay, Tasmania, Australia
      </li>
    </ul>
  </section>
</body>
</html>
```